Simple Logo Design for Semi-Clear Plastic Frosted Card stock

Create a business card on frosted plastic. compliment existing logo elements with a tree trunk, roots, or seed at the lower half and the full logo both on the front.

Contact information will go on a solid portion of the back of this design since this card stock is semi-transparent.

It is important to consider this plastic card stock medium in your design. I found helpful tips and guides listed at vellaprint-sample.net: be careful to understand ink printed on plastic cards cannot have too much of a consistent print area or risks peeling and fine lines can easily scratch off.
Updates

2" x 3.5" 20PT Clear Plastic Business cards with Round corners Please get info or templates here: https://www.vellaprint-sample.net/product-detail/2-x-35-20pt-clear-plastic-business-cards-with-round-corners

Target Market(s)

Not for profit- religion

Industry/Entity Type

Business

Must include complementary elements to the existing logo

Font styles to use
Decorative

Colors
000000

Requirements
Must have
• Elements of community, nature and oneness. Such as: seed, roots, tree trunk, etc.
• Three lines of space on the back for Name, Title, Phone Number.
Nice to have
• I like a light use of decorative elements
Should not have
• No eyes, from faces or animals.

```html
<!DOCTYPE html>
<html lang="en">
<head>
<meta charset="utf-8">
<title>Steadfast Grove – Business Card</title>
<link rel="stylesheet" href="https://fonts.googleapis.com/css2?family=Questrial&family=Open+Sans:wght@400;600&display=swap">
<style>
  :root {
    --page-bg: #ebe8e4;
    --leaf-green: #4a9a48;
    --deep-teal: #1f6e6b;
    --mid-teal: #24706d;
    --band-black: #050505;
    --name-green: #55a84e;
    --text-white: #ffffff;
    --tagline-grey: #8c8c8c;
  }
  * { margin: 0; padding: 0; box-sizing: border-box; }
  html, body { width: 1200px; height: 900px; overflow: hidden; }
  body { background: var(--page-bg); position: relative; font-family: "Open Sans", sans-serif; }

  .card { position: absolute; border-radius: 16px; overflow: hidden; }

  /* Front */
  .card-front { left: 78px; top: 33px; width: 587px; height: 365px; }
  .front-band-top { position: absolute; left: 0; top: 0; width: 100%; height: 97px;
    background: linear-gradient(180deg, var(--leaf-green), #46964a); }
  .front-band-middle { position: absolute; left: 0; top: 97px; width: 100%; height: 186px; background: var(--band-black); }
  .front-band-bottom { position: absolute; left: 0; top: 283px; width: 100%; height: 82px;
    background: linear-gradient(180deg, #2a7a66, var(--mid-teal)); }

  .front-brand { position: absolute; left: 22px; top: 118px; width: 310px; text-align: center; }
  .brand-dot { display: block; width: 64px; height: 64px; border-radius: 50%;
    background: var(--mid-teal); margin: 0 auto 18px; }
  .front-brand .brand-name { font-family: "Questrial", sans-serif; font-size: 30px;
    color: var(--name-green); letter-spacing: 0.5px; white-space: nowrap; line-height: 1; }
  .front-brand .brand-tagline { font-family: "Questrial", sans-serif; font-size: 13px;
    color: var(--tagline-grey); letter-spacing: 1.3px; text-transform: uppercase; margin-top: 8px; }

  .contact { position: absolute; right: 36px; top: 150px; text-align: right; }
  .contact-name { font-size: 23px; font-weight: 600; color: var(--name-green); line-height: 1.2; }
  .contact-title { font-size: 15px; color: var(--text-white); margin-top: 2px; }
  .contact-phone { font-size: 14px; color: var(--text-white); margin-top: 24px;
    display: flex; align-items: center; justify-content: flex-end; gap: 8px; }
  .contact-phone svg { width: 13px; height: 13px; fill: var(--name-green); }

  /* Back */
  .card-back { left: 390px; top: 505px; width: 565px; height: 352px;
    background: linear-gradient(180deg, var(--leaf-green) 0%, #3f914f 40%, var(--deep-teal) 100%); }
  .back-brand { position: absolute; left: 0; top: 228px; width: 100%; text-align: center; }
  .back-brand .brand-name { font-family: "Questrial", sans-serif; font-size: 46px;
    color: var(--text-white); letter-spacing: 1px; line-height: 1; white-space: nowrap; }
  .back-brand .brand-tagline { font-family: "Questrial", sans-serif; font-size: 18px;
    color: var(--text-white); letter-spacing: 1.5px; text-transform: uppercase; margin-top: 10px; }
</style>
</head>
<body>
  <section class="card card-front" aria-label="Card front">
    <div class="front-band-top"></div>
    <div class="front-band-middle"></div>
    <div class="front-band-bottom"></div>

    <div class="front-brand">
      <span class="brand-dot"></span>
      <p class="brand-name">STEADFAST GROVE</p>
      <p class="brand-tagline">Wisdom, Fellowship &amp; Rest</p>
    </div>

    <div class="contact">
      <p class="contact-name">Daniel Mercer</p>
      <p class="contact-title">Managing Director</p>
      <p class="contact-phone">(055)-318-2046
        <svg viewBox="0 0 24 24" aria-hidden="true"><path d="M6.6 10.8a15.1 15.1 0 0 0 6.6 6.6l2.2-2.2a1 1 0 0 1 1-.25 11.4 11.4 0 0 0 3.6.57 1 1 0 0 1 1 1V20a1 1 0 0 1-1 1A17 17 0 0 1 3 4a1 1 0 0 1 1-1h3.5a1 1 0 0 1 1 1c0 1.25.2 2.45.57 3.57a1 1 0 0 1-.25 1z"/></svg>
      </p>
    </div>
  </section>

  <section class="card card-back" aria-label="Card back">
    <div class="back-brand">
      <p class="brand-name">STEADFAST GROVE</p>
      <p class="brand-tagline">Wisdom, Fellowship &amp; Rest</p>
    </div>
  </section>
</body>
</html>
```